Business card design for holistic health care clinic

We need a double-sided business card design for our holistic health care clinic that integrates our logo design and also its color scheme. My business is called Valmira. It is an integrative medicine clinic. You have already done the logo for me. Please ensure an elegant and upscale design that is not cluttered, but still has all the necessary information (please see below for details).

Target Market(s)

Wellness, fitness, rehabilitation for educated, well-traveled open-minded clients who are focused on natural, organic, balanced and preventive healthcare and lifestyle.

Industry/Entity Type

Medical

Contact Information for Business Card

Modern, clean.

Number of Pages Required

1 page

Font styles to use
Serif
Sans Serif

Colors

Designer to choose colors to be used in the design.

Requirements
Must have
• Logo on one side, all other information on the other side.
• Other information should include:
• Tobias Wrenfeld - DOE, CPT, LMT
• 4100 East Marrow Drive
• Austin, TX 78119
• 512 555 0148
• 818 555 0192
• info@ValmiraHealth.example
• t.wrenfeld@ValmiraHealth.example
Nice to have
• Darker background on front - but not totally black - shaded/dark gray.

```html
<!DOCTYPE html>
<html lang="en">
<head>
<meta charset="utf-8">
<title>Valmira – Business Card</title>
<link rel="stylesheet" href="https://fonts.googleapis.com/css2?family=Montserrat:wght@600;700&family=Nunito:wght@700&family=Work+Sans:wght@300;400&display=swap">
<style>
  :root {
    --brand-blue: #1890d0;
    --ink: #2f2f2f;
    --card-white: #ffffff;
    --card-dark: #2b2b2b;
    --swoosh-dark: #2a2a2a;
    --backdrop: #1b1b1b;
  }
  * { box-sizing: border-box; margin: 0; padding: 0; }
  html, body { width: 1200px; height: 930px; overflow: hidden; }
  body {
    background: var(--backdrop);
    position: relative;
    font-family: "Work Sans", Arial, sans-serif;
  }
  .card {
    position: absolute;
    left: 278px;
    width: 644px;
    height: 368px;
    border-radius: 24px;
    overflow: hidden;
  }
  .card--front { top: 76px; background: var(--card-white); }
  .card--back { top: 486px; background: var(--card-dark); }

  .brand-name {
    font-family: "Montserrat", Arial, sans-serif;
    font-weight: 700;
    color: var(--brand-blue);
    text-transform: uppercase;
    letter-spacing: 1px;
    line-height: 1;
  }
  .brand-tagline {
    font-family: "Nunito", Arial, sans-serif;
    font-weight: 700;
    color: var(--brand-blue);
    line-height: 1;
  }

  /* front */
  .front-brand { position: absolute; left: 29px; top: 78px; }
  .front-brand .brand-name { font-size: 58px; }
  .front-brand .brand-tagline { font-size: 16px; margin-top: 6px; padding-left: 3px; }

  .holder { position: absolute; right: 29px; top: 180px; text-align: right; }
  .holder-name {
    font-family: "Montserrat", Arial, sans-serif;
    font-weight: 700;
    font-size: 29px;
    color: var(--brand-blue);
    text-transform: uppercase;
    letter-spacing: -0.5px;
    line-height: 1;
  }
  .holder-credentials {
    font-weight: 400;
    font-size: 15px;
    color: var(--ink);
    margin-top: 4px;
    letter-spacing: 0.3px;
  }
  .divider {
    position: absolute;
    left: 29px; right: 29px; top: 234px;
    height: 1.5px;
    background: var(--brand-blue);
  }

  .contact-list { position: absolute; left: 29px; top: 262px; list-style: none; }
  .contact-list li {
    display: flex; align-items: center;
    height: 20px;
    font-size: 16px; font-weight: 300;
    color: var(--ink);
  }
  .contact-list svg { width: 11px; height: 11px; margin-right: 9px; flex: none; }

  .address {
    position: absolute; right: 29px; top: 262px;
    text-align: right;
    font-size: 16px; font-weight: 300;
    color: var(--ink);
    font-style: normal;
    line-height: 20px;
  }

  .swoosh { position: absolute; left: 0; top: 0; width: 644px; height: 368px; pointer-events: none; }

  /* back */
  .back-brand {
    position: absolute; left: 0; right: 0; top: 140px;
    text-align: center;
  }
  .back-brand .brand-name { font-size: 90px; }
  .back-brand .brand-tagline { font-size: 25px; margin-top: 14px; letter-spacing: 0.3px; }
</style>
</head>
<body>

<section class="card card--front" aria-label="Card front">
  <div class="front-brand">
    <div class="brand-name">Valmira</div>
    <div class="brand-tagline">Integrative Holistic Medicine</div>
  </div>

  <div class="holder">
    <div class="holder-name">Tobias Wrenfeld</div>
    <div class="holder-credentials">DOE, CPT, LMT</div>
  </div>

  <div class="divider"></div>

  <ul class="contact-list">
    <li>
      <svg viewBox="0 0 12 12" fill="var(--brand-blue)"><path d="M2.4 1 4 .6 5.2 3.2 4.1 4.2c.6 1.4 1.6 2.5 3 3.1l1-1.1 2.6 1.2-.4 1.6C10 10.8 8.5 11.3 6.6 10.3 3.8 8.8 1.8 6.4 1.2 3.8 1 2.6 1.5 1.5 2.4 1z"/></svg>
      512 555 0148
    </li>
    <li>
      <svg viewBox="0 0 12 12" fill="none" stroke="var(--brand-blue)" stroke-width="1.6"><rect x="3" y="0.8" width="6" height="10.4" rx="1"/><line x1="5" y1="9" x2="7" y2="9"/></svg>
      818 555 0192
    </li>
    <li>
      <svg viewBox="0 0 12 12" fill="none" stroke="var(--brand-blue)" stroke-width="1.4"><rect x="0.8" y="2.4" width="10.4" height="7.2" rx="0.8"/><polyline points="1,3 6,6.8 11,3"/></svg>
      info@ValmiraHealth.example
    </li>
    <li>
      <svg viewBox="0 0 12 12" fill="none" stroke="var(--brand-blue)" stroke-width="1.1"><circle cx="6" cy="6" r="5.2"/><ellipse cx="6" cy="6" rx="2.3" ry="5.2"/><line x1="0.8" y1="6" x2="11.2" y2="6"/><line x1="1.6" y1="3.4" x2="10.4" y2="3.4"/><line x1="1.6" y1="8.6" x2="10.4" y2="8.6"/></svg>
      t.wrenfeld@ValmiraHealth.example
    </li>
  </ul>

  <address class="address">
    4100 East Marrow Drive<br>
    Austin, TX 78119
  </address>

  <svg class="swoosh" viewBox="0 0 644 368" aria-hidden="true">
    <path d="M282 368 C 380 338 520 322 644 322 L 644 368 Z" fill="var(--swoosh-dark)"/>
    <path d="M318 368 C 420 340 540 326 644 324 L 644 368 Z" fill="var(--brand-blue)"/>
  </svg>
</section>

<section class="card card--back" aria-label="Card back">
  <div class="back-brand">
    <div class="brand-name">Valmira</div>
    <div class="brand-tagline">Integrative Holistic Medicine</div>
  </div>
</section>

</body>
</html>
```